interior designer/stylist looking for a letter press business card to reflect the stylish work

Hello Designers,
I need a business card design for an company called Mosaic Interior Design. I'm aiming at the high end residential and private client market in London providing sleek simple interiors. I'd like my business card to be pinterest worthy and expensive looking, i want people to pin it and for it to have a sought after look, and want prospective customers to hire me as their interior designer as my card is so beautiful.
I love letter press design. I also like the use of colour/foil on the edge.
Colour combos & general things I like -
Black and White
Navy Blue and Gold
Neutral colours (muted palette of greys whites navys beiges)
White Marble & brass
Vorelle (fashion designer)
....also open to other suggestions....
Please dont take the pink in the attached photos too literally. i'd like the card to look more masculine than feminine.
I'd like Mosaic on one side in one font, with interior design underneath so one word will make the statement....... unless anyone has any other ideas, open to suggestions.
I'd like a really simple font and for the whole card to look very graphic.
my details -
Petra Wendlecombe
Interior Designer & Stylist
email petra@mosaicinteriordesign.co.uk
phone +447311584209
website wwww.mosaicinteriordesign.co.uk
GO GO GO!! EXCITED TO SEE THE OUTCOME!!
x P
Target Market(s)
High End Residential and private clients
Industry/Entity Type
Business
Contact Information for Business Card
Mosaic Interior Design & Styling
Petra Wendlecombe
phone +447311584209

```html
<!DOCTYPE html>
<html lang="en">
<head>
<meta charset="utf-8">
<title>Petra Wendlecombe — Business Card</title>
<link rel="stylesheet" href="https://fonts.googleapis.com/css2?family=Azeret+Mono:wght@200&family=Share+Tech+Mono&display=swap">
<style>
  :root {
    --paper: #ffffff;
    --ink: #3a3a3a;
    --gold-light: #f3dc8e;
    --gold-mid: #dcb95a;
    --gold-deep: #c89b36;
    --frame: 12px;
  }
  * { margin: 0; padding: 0; box-sizing: border-box; }
  html, body {
    width: 1200px;
    height: 686px;
    overflow: hidden;
    background: var(--paper);
  }
  .card {
    position: relative;
    width: 1200px;
    height: 686px;
    background:
      linear-gradient(135deg, var(--gold-light) 0%, var(--gold-mid) 30%, var(--gold-deep) 55%, var(--gold-light) 75%, var(--gold-mid) 100%);
    padding: var(--frame);
  }
  .card__face {
    position: relative;
    width: 100%;
    height: 100%;
    background: var(--paper);
    color: var(--ink);
    text-align: center;
  }
  .card__name {
    position: absolute;
    left: 0; right: 0;
    top: 200px;
    font-family: "Azeret Mono", monospace;
    font-weight: 200;
    font-size: 86px;
    letter-spacing: 3px;
    line-height: 1;
  }
  .card__role {
    position: absolute;
    left: 0; right: 0;
    top: 312px;
    font-family: "Share Tech Mono", monospace;
    font-size: 27px;
    letter-spacing: 3px;
    line-height: 1;
  }
  .card__contact {
    position: absolute;
    left: 0; right: 0;
    top: 436px;
    font-family: "Share Tech Mono", monospace;
    font-size: 26px;
    letter-spacing: 3px;
    line-height: 34px;
  }
  .card__divider { margin: 0 18px; }
</style>
</head>
<body>
  <div class="card">
    <div class="card__face">
      <h1 class="card__name">Petra Wendlecombe</h1>
      <p class="card__role">INTERIOR DESIGNER &amp; STYLIST</p>
      <div class="card__contact">
        <p>petra@mosaicinteriordesign.co.uk<span class="card__divider">|</span>+447311584209</p>
        <p>wwww.mosaicinteriordesign.co.uk</p>
      </div>
    </div>
  </div>
</body>
</html>
```